Business Card - connecting 2 souls and beggining the journey of self discovery

Logo on the front
with tag line

On the back list of services and contact details

Seminars
workshops
Coaching
podcasts

Darren Whitlow
Health & Wellbeing Life Coach
0491 372 615
darren@brightcoreliving.example
brightcoreliving.example

Industry/Entity Type

Life Coaching

Contact Information for Business Card

I like the use of colour from the logo to be used. I'm not a fan of white.

Requirements
Must have
• My tagline: The journey home starts with you
Nice to have
• Use of colour that is in the mind body soul logo

```html
<!DOCTYPE html>
<html lang="en">
<head>
<meta charset="utf-8">
<title>Bright Core Living – Business Card</title>
<link href="https://fonts.googleapis.com/css2?family=Montserrat:wght@500;600;700&family=Open+Sans:wght@400;600&display=swap" rel="stylesheet">
<style>
  :root {
    --bg: #2b2b2b;
    --orange: #f7a021;
    --white: #ffffff;
    --purple: #7b3f98;
    --grey: #6d6e71;
    --green: #8cc63f;
    --yellow: #f4d03f;
    --pink: #ef5f78;
    --teal: #2bb5a0;
  }
  * { margin: 0; padding: 0; box-sizing: border-box; }
  html, body { width: 1200px; height: 864px; overflow: hidden; }
  body {
    background: var(--bg);
    font-family: "Open Sans", sans-serif;
    position: relative;
  }
  .card {
    position: absolute;
    width: 540px;
    height: 309px;
    border-radius: 22px;
    overflow: hidden;
    box-shadow: 0 14px 30px rgba(0,0,0,.45);
  }
  /* Front */
  .card-front {
    left: 40px; top: 278px;
    background: var(--orange);
    display: flex; flex-direction: column; align-items: center; justify-content: center;
    color: var(--white);
  }
  .brand {
    display: flex; align-items: center; gap: 14px;
    font-family: "Montserrat", sans-serif;
    font-weight: 600;
    letter-spacing: -0.5px;
  }
  .brand-dot {
    border-radius: 50%;
    flex-shrink: 0;
  }
  .card-front .brand { font-size: 34px; }
  .card-front .brand-dot { width: 34px; height: 34px; background: var(--white); }
  .tagline {
    margin-top: 28px;
    font-size: 14px;
    letter-spacing: 0.3px;
  }
  /* Back */
  .card-back {
    left: 620px; top: 278px;
    background: var(--white);
  }
  .back-brand {
    position: absolute; left: 30px; top: 112px;
  }
  .card-back .brand { font-size: 21px; color: var(--grey); gap: 10px; }
  .card-back .brand-dot { width: 22px; height: 22px; background: var(--purple); }
  .divider {
    position: absolute; left: 276px; top: 52px;
    width: 1.5px; height: 150px;
    background: var(--green);
  }
  .contact { position: absolute; left: 300px; top: 58px; }
  .contact-name {
    font-family: "Montserrat", sans-serif;
    font-weight: 700; font-size: 22px;
    color: var(--purple);
  }
  .contact-role { font-size: 13px; color: var(--grey); margin-top: 1px; }
  .contact-list { list-style: none; margin-top: 22px; }
  .contact-list li {
    display: flex; align-items: center; gap: 8px;
    font-size: 12.5px; color: var(--grey); line-height: 21px;
  }
  .contact-list svg { width: 13px; height: 13px; flex-shrink: 0; }
  .services {
    position: absolute; left: 0; right: 0; bottom: 30px;
    display: flex; justify-content: center; align-items: center; gap: 10px;
    font-size: 15px; color: var(--grey);
  }
  .services .sep { width: 5px; height: 5px; border-radius: 50%; }
  .band {
    position: absolute; left: 0; right: 0; bottom: 0; height: 10px;
    background: linear-gradient(90deg, var(--green), var(--purple) 35%, var(--yellow) 60%, var(--orange) 80%, var(--pink));
  }
</style>
</head>
<body>
  <section class="card card-front">
    <div class="brand"><span class="brand-dot"></span>Bright Core Living</div>
    <p class="tagline">The journey home starts with you</p>
  </section>

  <section class="card card-back">
    <div class="back-brand">
      <div class="brand"><span class="brand-dot"></span>Bright Core Living</div>
    </div>
    <div class="divider"></div>
    <div class="contact">
      <h1 class="contact-name">Darren Whitlow</h1>
      <p class="contact-role">Life Coach</p>
      <ul class="contact-list">
        <li>
          <svg viewBox="0 0 24 24"><path fill="#f7a021" d="M6.6 10.8a15.1 15.1 0 0 0 6.6 6.6l2.2-2.2a1 1 0 0 1 1-.25 11.4 11.4 0 0 0 3.6.57 1 1 0 0 1 1 1V20a1 1 0 0 1-1 1A17 17 0 0 1 3 4a1 1 0 0 1 1-1h3.5a1 1 0 0 1 1 1c0 1.25.2 2.45.57 3.57a1 1 0 0 1-.25 1z"/></svg>
          0491 372 615
        </li>
        <li>
          <svg viewBox="0 0 24 24" fill="none" stroke="#f7a021" stroke-width="2"><rect x="3" y="5" width="18" height="14" rx="1"/><path d="M3 6l9 7 9-7"/></svg>
          darren@brightcoreliving.example
        </li>
        <li>
          <svg viewBox="0 0 24 24" fill="none" stroke="#f7a021" stroke-width="2"><circle cx="12" cy="12" r="9"/><path d="M3 12h18M12 3c3 3 3 15 0 18M12 3c-3 3-3 15 0 18"/></svg>
          brightcoreliving.example
        </li>
      </ul>
    </div>
    <div class="services">
      <span>Seminars</span><span class="sep" style="background:var(--purple)"></span>
      <span>Workshops</span><span class="sep" style="background:var(--green)"></span>
      <span>Coaching</span><span class="sep" style="background:var(--orange)"></span>
      <span>Podcasts</span>
    </div>
    <div class="band"></div>
  </section>
</body>
</html>
```